Beacon Advisory Website

I currently have a website www.beaconadvisoryinc.com. We are a IT Consulting Company. Our website will pretty much tell out our services. I am looking to enhance my website and make it look more professional. Looking for very classy and Contemporary look and design for my website.

It Company

```html
<!DOCTYPE html>
<html lang="en">
<head>
<meta charset="utf-8">
<title>Beacon Advisory</title>
<link rel="stylesheet" href="https://fonts.googleapis.com/css2?family=Open+Sans:wght@400;600;700&family=Roboto:wght@400;500&display=swap">
<style>
:root{
  --brand:#1a63a8;
  --brand-light:#2a9bd8;
  --ink:#111111;
  --text:#555555;
  --white:#ffffff;
  --band:#ebebeb;
  --footer:#3a3a3a;
  --footer-base:#2b2b2b;
  --footer-text:#e6e6e6;
}
*{margin:0;padding:0;box-sizing:border-box}
html,body{width:1200px;height:2323px;overflow:hidden;background:var(--white)}
body{position:relative;font-family:"Open Sans",Arial,sans-serif;color:var(--text)}
.abs{position:absolute}

/* header */
.site-header{left:0;top:0;width:1200px;height:116px;background:var(--white)}
.brand{left:100px;top:38px;display:flex;align-items:center;gap:12px}
.brand-mark{width:40px;height:40px;border-radius:50%;background:var(--brand)}
.brand-name{font-family:"Roboto",Arial,sans-serif;font-weight:500;font-size:30px;color:var(--brand);letter-spacing:.5px}
.call{right:104px;top:40px;text-align:right}
.call-label{font-size:14px;color:var(--brand-light);line-height:20px}
.call-number{font-size:18px;color:var(--ink);line-height:24px}
.call-icon{left:900px;top:54px}

/* nav */
.main-nav{left:0;top:116px;width:1200px;height:67px;background:var(--brand);display:flex;justify-content:center;gap:50px;align-items:center}
.main-nav a{color:var(--white);text-decoration:none;font-family:"Roboto",Arial,sans-serif;font-size:17px;letter-spacing:.2px}

/* hero */
.hero{left:0;top:183px;width:1200px;height:676px;background:linear-gradient(100deg,#3a3f4a 0%,#6d6a66 25%,#b8b2a8 45%,#d9d8d4 65%,#eceae6 100%)}
.hero-title{right:76px;top:405px;text-align:right;font-family:"Roboto",Arial,sans-serif;font-size:46px;line-height:53px;color:var(--ink)}

/* features */
.features{left:77px;top:680px;width:1045px;height:249px;background:var(--white);display:flex;box-shadow:0 10px 24px rgba(0,0,0,.12)}
.feature{flex:1;position:relative;border-right:1px solid #e5e5e5}
.feature:last-child{border-right:none}
.feature-icon{position:absolute;left:28px;top:46px}
.feature-title{position:absolute;left:81px;top:45px;font-family:"Roboto",Arial,sans-serif;font-size:20px;color:var(--ink)}
.feature-text{position:absolute;left:81px;top:86px;width:240px;font-size:14.5px;line-height:25px;color:var(--text)}
.read-link{position:absolute;left:81px;top:190px;font-size:15px;color:var(--brand)}

/* welcome */
.welcome-title{left:80px;top:1025px;font-family:"Roboto",Arial,sans-serif;font-size:38px;color:var(--ink)}
.welcome-title span{color:var(--brand)}
.welcome-text{left:80px;top:1103px;width:720px;font-size:15.5px;line-height:25px}
.welcome-text p+p{margin-top:25px}
.button{left:79px;top:1268px;width:112px;height:35px;background:var(--brand);color:var(--white);font-size:15px;display:flex;align-items:center;justify-content:center}
.welcome-photo{left:797px;top:985px;width:290px;height:315px;border-radius:50%;background:radial-gradient(circle,#eeeae3 0%,#c9ccd2 45%,#5a6678 75%,rgba(255,255,255,0) 78%)}

/* services */
.services{left:0;top:1382px;width:1200px;height:584px;background:var(--band)}
.services-title{left:0;top:1408px;width:1200px;text-align:center;font-family:"Roboto",Arial,sans-serif;font-size:38px;color:var(--brand)}
.service{top:1502px;width:311px;height:394px;background:var(--white)}
.service-photo{width:311px;height:218px}
.service-title{position:absolute;left:22px;top:238px;font-family:"Roboto",Arial,sans-serif;font-size:19px;color:var(--ink)}
.service-text{position:absolute;left:22px;top:278px;width:250px;font-size:14.5px;line-height:25px}

/* footer */
.site-footer{left:0;top:1966px;width:1200px;height:291px;background:var(--footer);color:var(--footer-text)}
.footer-heading{font-size:20px;color:var(--white);top:2022px}
.contact-line{font-size:14.5px;line-height:23px;left:149px}
.quick-links{left:446px;top:2060px;list-style:none}
.quick-links li{font-size:12.5px;line-height:28.5px;color:var(--footer-text)}
.social{left:695px;top:2064px;list-style:none}
.social li{display:flex;align-items:center;gap:18px;height:42.5px;font-size:13px}
.social-dot{width:11px;height:11px;border-radius:50%;background:var(--footer-text)}
.footer-brand{left:890px;top:2076px;display:flex;align-items:center;gap:10px}
.footer-brand .brand-mark{width:34px;height:34px;background:#2b2b2b}
.footer-brand .brand-name{font-size:24px;color:#262626}
.footer-base{left:0;top:2257px;width:1200px;height:66px;background:var(--footer-base);color:var(--white);font-size:15px;display:flex;align-items:center;justify-content:center}
.footer-base strong{font-weight:700;margin:0 4px}
</style>
</head>
<body>

<header class="site-header abs">
  <div class="brand abs"><span class="brand-mark"></span><span class="brand-name">Beacon Advisory</span></div>
  <svg class="call-icon abs" width="38" height="38" viewBox="0 0 38 38" aria-hidden="true">
    <circle cx="19" cy="19" r="18" fill="none" stroke="#2a9bd8" stroke-width="1.5"/>
    <path d="M13 12c1-1 2-1 3 0l2 3c.5 1 0 2-1 2.5 1 2 2.5 3.5 4.5 4.5.5-1 1.5-1.5 2.5-1l3 2c1 1 1 2 0 3l-1.5 1.5c-5 0-12-7-12-12z" fill="#2a9bd8"/>
  </svg>
  <div class="call abs">
    <div class="call-label">Call Us Now</div>
    <div class="call-number">+1 (555) 014 2290</div>
  </div>
</header>

<nav class="main-nav abs">
  <a href="#">COMPANY</a><a href="#">SERVICES</a><a href="#">SOLUTION</a><a href="#">RESOURCES</a><a href="#">CAREER</a><a href="#">CONTACT US</a>
</nav>

<section class="hero abs" role="img" aria-label="Photo of two smiling businessmen looking at a laptop in a bright office"></section>
<h1 class="hero-title abs">GET THE BEST SOLUTION<br>FOR YOUR BUSSINESS</h1>

<section class="features abs">
  <article class="feature">
    <svg class="feature-icon" width="40" height="40" viewBox="0 0 40 40" aria-hidden="true">
      <circle cx="20" cy="20" r="18" fill="none" stroke="#1a63a8" stroke-width="2.5"/>
      <circle cx="20" cy="20" r="13" fill="none" stroke="#1a63a8" stroke-width="1" stroke-dasharray="2 3"/>
      <path d="M20 20 L20 8" stroke="#1a63a8" stroke-width="2.5"/><circle cx="20" cy="21" r="3" fill="#1a63a8"/>
    </svg>
    <h3 class="feature-title">Dashboard</h3>
    <p class="feature-text">Dashboards are a key component of every organization's Performance Management .</p>
    <a class="read-link">Read More</a>
  </article>
  <article class="feature">
    <svg class="feature-icon" width="42" height="46" viewBox="0 0 42 46" aria-hidden="true">
      <ellipse cx="21" cy="6" rx="19" ry="5" fill="#1a63a8"/>
      <rect x="2" y="12" width="38" height="8" rx="4" fill="#1a63a8"/>
      <rect x="2" y="23" width="38" height="8" rx="4" fill="#1a63a8"/>
      <rect x="18" y="31" width="6" height="14" fill="#1a63a8"/><rect x="12" y="36" width="18" height="5" fill="#1a63a8"/>
    </svg>
    <h3 class="feature-title">Data warehousing</h3>
    <p class="feature-text">A data warehouse is the concept of data extracted from operational systems and made available as historical snapshots</p>
    <a class="read-link">Read More</a>
  </article>
  <article class="feature">
    <svg class="feature-icon" width="42" height="38" viewBox="0 0 42 38" aria-hidden="true">
      <rect x="15" y="1" width="12" height="10" fill="#1a63a8"/>
      <path d="M21 11v8M6 19h30M6 19v7M21 19v7M36 19v7" stroke="#1a63a8" stroke-width="2.5" fill="none"/>
      <rect x="0" y="26" width="12" height="10" fill="#1a63a8"/><rect x="15" y="26" width="12" height="10" fill="#1a63a8"/><rect x="30" y="26" width="12" height="10" fill="#1a63a8"/>
    </svg>
    <h3 class="feature-title">BPM</h3>
    <p class="feature-text">Beacon Advisory having Apex Certified Consultants in to provide Business Process Management .</p>
    <a class="read-link">Read More</a>
  </article>
</section>

<h2 class="welcome-title abs">WELCOME TO <span>BEACON ADVISORY</span></h2>
<div class="welcome-text abs">
  <p>Delivers highest level of Quality Consultants and services for the lowest Cost of Ownership. Forge Client relationships to better understand and respond to their business needs.</p>
  <p>Forget&nbsp; Client relationships to better understand and respond to their business needs.Develop, challenge, empower and recognize our employees .</p>
</div>
<a class="button abs">Read More</a>
<div class="welcome-photo abs" role="img" aria-label="Overhead photo of a team meeting around a conference table"></div>

<section class="services abs"></section>
<h2 class="services-title abs">SERVICES</h2>
<article class="service abs" style="left:101px">
  <div class="service-photo" role="img" aria-label="Photo of a chalkboard with training related words" style="background:linear-gradient(135deg,#1c3a48,#2f5a6a 55%,#17303c)"></div>
  <h3 class="service-title">TECHNOLOGY</h3>
  <p class="service-text">Beacon Advisory Training programs are perfect&nbsp; to e&nbsp; nhance their careers.</p>
</article>
<article class="service abs" style="left:449px">
  <div class="service-photo" role="img" aria-label="Photo of people signing documents at a desk" style="background:linear-gradient(135deg,#5e4a3c,#a88f78 50%,#e4dcd2)"></div>
  <h3 class="service-title">OFFSHORE</h3>
  <p class="service-text">Our Offshore development model has a unique distinction&nbsp; software solutions</p>
</article>
<article class="service abs" style="left:790px">
  <div class="service-photo" role="img" aria-label="Photo of a globe made of puzzle pieces" style="background:linear-gradient(135deg,#e6eef6,#9fb6cf 55%,#4f6f96)"></div>
  <h3 class="service-title">APPLICATON DEVLOPMENT</h3>
  <p class="service-text">Drawing on our experience in all major industries,</p>
</article>

<footer class="site-footer abs"></footer>
<h4 class="footer-heading abs" style="left:119px">Contact Us</h4>
<svg class="abs" style="left:115px;top:2070px" width="12" height="16" viewBox="0 0 12 16" aria-hidden="true"><path d="M6 0a6 6 0 0 1 6 6c0 4-6 10-6 10S0 10 0 6a6 6 0 0 1 6-6z" fill="#fff"/><circle cx="6" cy="6" r="2.2" fill="#3a3a3a"/></svg>
<div class="contact-line abs" style="top:2061px">2040 Harbor Lane<br>Suite 310<br>Westfield, NJ 07090</div>
<svg class="abs" style="left:117px;top:2146px" width="16" height="16" viewBox="0 0 16 16" aria-hidden="true"><path d="M2 1c1-1 2-1 3 0l2 3c.5 1 0 2-1 2.5 1 2 2.5 3.5 4.5 4.5.5-1 1.5-1.5 2.5-1l2 1.5c1 1 1 2 0 3L14 16C8 16 0 8 0 3z" fill="#fff"/></svg>
<div class="contact-line abs" style="top:2143px">+1 (555) 014 2290</div>
<svg class="abs" style="left:116px;top:2186px" width="17" height="12" viewBox="0 0 17 12" aria-hidden="true"><rect x=".75" y=".75" width="15.5" height="10.5" fill="none" stroke="#fff" stroke-width="1.5"/><path d="M1 1l7.5 6L16 1" fill="none" stroke="#fff" stroke-width="1.5"/></svg>
<div class="contact-line abs" style="top:2181px">info@beaconadvisory.com</div>

<h4 class="footer-heading abs" style="left:446px">Quick Links</h4>
<ul class="quick-links abs">
  <li>COMPANY</li><li>SERVICES</li><li>SOLUTION</li><li>RESOURCES</li><li>CAREER</li><li>CONTACT US</li>
</ul>

<h4 class="footer-heading abs" style="left:695px">Follow Us On</h4>
<ul class="social abs">
  <li><span class="social-dot"></span>Community</li>
  <li><span class="social-dot"></span>Network</li>
  <li><span class="social-dot"></span>Updates</li>
</ul>

<div class="footer-brand abs"><span class="brand-mark"></span><span class="brand-name">Beacon Advisory</span></div>

<div class="footer-base abs">©<strong>BEACON ADVISORY</strong>-2016.All Rights Reserved.</div>

</body>
</html>
```